Global Yoga Apparel Brand Needs a Beautiful Website

We need a website design for a new Yoga brand called Vey. We develop beautiful, stylish, sexy, comfortable yoga leggings, tops, and yoga apparel for women looking to feel their best, look their best and perform their best on and off the yoga mat.
This will go up at http://vey.example/ (which is a landing page right now).
We would like to see simple and clean design where the focus will be on powerful images and clean background space. We will be using Shopify to start building on and here are three sites that we would love to see options based off of the look, layout and feel while making something unique at the same time:
1. Dunt.ca
2. parvasini.com
3. www.k-mole.com
The final design should look clean, beautiful, inspiring, powerful and empowering.
Target Market(s)
mostly Females 21-35 range but will be appealing to women over 35 as well.

```html
<!DOCTYPE html>
<html lang="en">
<head>
<meta charset="utf-8">
<title>Vey — Yoga Apparels</title>
<link rel="stylesheet" href="https://fonts.googleapis.com/css2?family=Poppins:wght@400;500;600;700&family=Questrial&display=swap">
<style>
:root{
  --ink:#000;
  --bar:#2b2b2b;
  --white:#fff;
  --hero-bg:#ebebeb;
  --floor-a:#e6d9c4;
  --floor-b:#cfbd9f;
  --card-bg:#f6f6f6;
  --card-line:#dcdcdc;
  --band:#f5f5f5;
  --text:#222;
  --muted:#666;
  --star:#444;
  --star-off:#bbb;
  --btn-grey:#c9c9c9;
  --foot-text:#e8e8e8;
  --foot-line:#555;
}
*{box-sizing:border-box;margin:0;padding:0}
html,body{width:1200px;height:2663px;overflow:hidden}
body{position:relative;background:var(--white);font-family:"Questrial",sans-serif;color:var(--text)}
.abs{position:absolute}
svg{display:block}

/* top bar */
.topbar{left:0;top:0;width:1200px;height:32px;background:var(--bar);color:#ddd;font-size:13px}
.topbar ul{list-style:none;display:flex;gap:36px;position:absolute;right:30px;top:8px}
.topbar li{display:flex;align-items:center;gap:8px}

/* header */
.header{left:0;top:32px;width:1200px;height:99px;background:var(--ink);color:var(--white)}
.brand{position:absolute;left:83px;top:14px;font-family:"Poppins",sans-serif;font-weight:600;font-size:58px;letter-spacing:1px;line-height:1}
.nav{position:absolute;left:389px;top:50px;display:flex;align-items:center;font-family:"Poppins",sans-serif;font-weight:500;font-size:16px}
.nav a{color:var(--white);text-decoration:none;padding:3px 13px;border-left:1px solid #555;line-height:20px}
.nav a:first-child{border:2px solid var(--white);border-radius:2px;margin-right:16px}
.nav a:nth-child(2){border-left:0}
.search{position:absolute;left:1084px;top:80px;width:36px;height:30px;background:var(--white);border-radius:2px;display:flex;align-items:center;justify-content:center}

/* hero */
.hero{left:0;top:131px;width:1200px;height:572px;background:var(--hero-bg);overflow:hidden}
.floor{position:absolute;left:0;bottom:0;width:1200px;height:126px;background:linear-gradient(180deg,var(--floor-a),var(--floor-b))}
.hero-photo{position:absolute;left:186px;top:41px;width:435px;height:471px;background:radial-gradient(ellipse at 50% 45%,#3a3a3a 0,#1a1a1a 55%,rgba(26,26,26,0) 72%)}
.hero-mark{position:absolute;left:893px;top:118px;font-family:"Poppins",sans-serif;font-weight:600;font-size:96px;color:#d6d6d6;line-height:1}
.hero-title{position:absolute;right:149px;top:243px;font-family:"Poppins",sans-serif;font-weight:700;font-size:48px;color:var(--ink);line-height:1}
.hero-sub{position:absolute;right:149px;top:320px;font-size:19px;color:#111}
.hero-btn{position:absolute;left:893px;top:364px;width:158px;height:39px;background:var(--ink);color:var(--white);font-family:"Poppins",sans-serif;font-weight:600;font-size:17px;display:flex;align-items:center;justify-content:center}
.hero-arrows{position:absolute;left:1010px;top:426px;display:flex;gap:3px}
.hero-arrows span{width:18px;height:18px;border:1px solid #333;background:var(--white);display:flex;align-items:center;justify-content:center}

/* section titles */
.section-title{left:0;width:1200px;text-align:center;font-family:"Poppins",sans-serif;font-weight:600;font-size:30px;color:var(--ink)}
.divider{left:515px;width:170px;height:18px}

/* cards */
.grid{left:84px;width:1032px;display:grid;grid-template-columns:repeat(4,246px);gap:16px 16px}
.cat-card{height:220px;background:var(--card-bg);border:1px solid var(--card-line);padding:8px}
.card-img{height:150px;border:1px solid var(--card-line)}
.cat-card h3{text-align:center;font-family:"Poppins",sans-serif;font-weight:600;font-size:19px;margin-top:23px;color:var(--ink)}
.prod-card{height:302px;background:var(--card-bg);border:1px solid var(--card-line);padding:8px}
.prod-card h4{font-family:"Poppins",sans-serif;font-weight:600;font-size:15px;margin-top:13px;color:var(--ink)}
.rating{display:flex;align-items:center;gap:16px;font-size:11px;margin-top:4px}
.stars{display:flex;gap:1px}
.price{font-family:"Poppins",sans-serif;font-weight:600;font-size:17px;margin-top:6px;color:var(--ink)}
.actions{display:flex;gap:6px;margin-top:14px}
.add-cart{height:30px;width:120px;border:1px solid #555;border-radius:3px;background:var(--white);display:flex;align-items:center;font-size:11px}
.add-cart .ic{width:28px;height:100%;border-right:1px solid #555;display:flex;align-items:center;justify-content:center}
.add-cart span{flex:1;text-align:center}
.sq{width:36px;height:30px;background:var(--btn-grey);border-radius:3px;display:flex;align-items:center;justify-content:center}

/* newsletter band */
.band{left:0;top:1912px;width:1200px;height:239px;background:var(--band);text-align:center}
.band h2{font-family:"Poppins",sans-serif;font-weight:600;font-size:25px;letter-spacing:1px;margin-top:57px;color:var(--ink)}
.band p{font-size:14px;color:var(--muted);margin-top:10px}
.band .btn{display:inline-flex;align-items:center;justify-content:center;width:151px;height:37px;background:var(--ink);color:var(--white);font-family:"Poppins",sans-serif;font-weight:600;font-size:16px;margin-top:22px}

/* service boxes */
.services{left:256px;top:2206px;display:flex;gap:40px}
.service{width:202px;height:110px;border:5px double var(--ink);outline:1px dashed #999;outline-offset:-9px;text-align:center;padding-top:14px}
.service svg{margin:0 auto}
.service h5{font-family:"Poppins",sans-serif;font-weight:500;font-size:13px;margin-top:6px;color:var(--ink)}
.service p{font-size:11px;margin-top:3px;color:#333}

/* footer */
.footer{left:0;top:2370px;width:1200px;height:243px;background:var(--ink);color:var(--foot-text)}
.fcol{position:absolute;top:40px}
.fcol h6{font-family:"Poppins",sans-serif;font-weight:500;font-size:14px;color:var(--white);padding-bottom:10px;border-bottom:1px solid #333;width:150px}
.fcol ul{list-style:none;margin-top:16px}
.fcol li{font-size:12px;line-height:22.6px;display:flex;align-items:center;gap:10px}
.fcol li::before{content:"";border-left:5px solid var(--white);border-top:4px solid transparent;border-bottom:4px solid transparent}
.vsep{position:absolute;top:30px;height:190px;border-left:1px dotted var(--foot-line)}
.news p{font-size:13.5px;line-height:20px;width:270px;margin-top:20px;color:var(--white)}
.news .field{width:259px;height:30px;background:var(--white);color:#666;font-size:11px;padding:8px 10px;margin-top:12px}
.news .submit{width:71px;height:31px;background:#555;color:var(--white);font-size:15px;display:flex;align-items:center;justify-content:center;margin-top:12px;border:1px solid #888}
.foot-brand{position:absolute;left:1000px;top:54px;font-family:"Poppins",sans-serif;font-weight:600;font-size:58px;color:var(--white);line-height:1}
.social{position:absolute;left:987px;top:167px;display:flex;gap:9px}
.social span{width:26px;height:26px;background:#555;border-radius:2px}
.bottombar{left:0;top:2613px;width:1200px;height:50px;background:var(--bar);color:#ddd;font-size:13px}
.copy{position:absolute;left:83px;top:17px}
.accept{position:absolute;left:834px;top:13px;display:flex;align-items:center;gap:6px}
.accept b{font-weight:400;margin-right:8px}
.card-pay{width:36px;height:22px;background:var(--white);border-radius:2px;color:#333;font-size:9px;display:flex;align-items:center;justify-content:center}
</style>
</head>
<body>

<div class="abs topbar">
  <ul>
    <li><svg width="14" height="12" viewBox="0 0 14 12"><path d="M1 1h2l2 7h7l1-5H4" fill="none" stroke="#ddd" stroke-width="1.4"/><circle cx="6" cy="10.5" r="1" fill="#ddd"/><circle cx="11" cy="10.5" r="1" fill="#ddd"/></svg>View Cart (0)</li>
    <li><svg width="12" height="12" viewBox="0 0 12 12"><rect x="1" y="1" width="10" height="10" fill="none" stroke="#ddd" stroke-width="1.4"/><path d="M3 4h6M3 6h6M3 8h4" stroke="#ddd"/></svg>Register</li>
    <li><svg width="13" height="12" viewBox="0 0 13 12"><path d="M7 1h5v10H7" fill="none" stroke="#ddd" stroke-width="1.4"/><path d="M1 6h7M5 3l3 3-3 3" fill="none" stroke="#ddd" stroke-width="1.4"/></svg>Login</li>
  </ul>
</div>

<header class="abs header">
  <div class="brand">vey</div>
  <nav class="nav">
    <a>Home</a><a>About</a><a>Inspiration</a><a>Featured Products</a><a>Blog</a><a>Contact Us</a>
  </nav>
</header>
<div class="search abs"><svg width="16" height="16" viewBox="0 0 16 16"><circle cx="6.5" cy="6.5" r="4.5" fill="none" stroke="#000" stroke-width="2"/><path d="M10 10l4 4" stroke="#000" stroke-width="2.5"/></svg></div>

<section class="abs hero">
  <div class="floor"></div>
  <div class="hero-photo" role="img" aria-label="Woman in black yoga wear seated in a twisted yoga pose on a wooden floor"></div>
  <div class="hero-mark">vey</div>
  <h1 class="hero-title">Yoga Apparels</h1>
  <p class="hero-sub">Stretchable fabrics enhance yoga postures</p>
  <div class="hero-btn">Shop Now</div>
  <div class="hero-arrows">
    <span><svg width="6" height="8"><path d="M6 0v8L0 4z" fill="#000"/></svg></span>
    <span><svg width="6" height="8"><path d="M0 0v8l6-4z" fill="#000"/></svg></span>
  </div>
</section>

<h2 class="abs section-title" style="top:752px">Categories</h2>
<svg class="abs divider" style="top:807px" viewBox="0 0 170 18"><path d="M0 9h72M98 9h72" stroke="#ccc"/><circle cx="85" cy="9" r="6" fill="none" stroke="#ccc"/><circle cx="85" cy="9" r="2.5" fill="none" stroke="#ccc"/></svg>

<div class="abs grid" style="top:859px">
  <div class="cat-card"><div class="card-img" role="img" aria-label="Grey yoga leggings" style="background:linear-gradient(#fff,#e4e4e4)"></div><h3>Yoga leggings</h3></div>
  <div class="cat-card"><div class="card-img" role="img" aria-label="Black yoga sports top" style="background:linear-gradient(#fff,#e2d7cf)"></div><h3>Yoga tops</h3></div>
  <div class="cat-card"><div class="card-img" role="img" aria-label="Black yoga capri with green waistband" style="background:linear-gradient(#fff,#e0e0e0)"></div><h3>Yoga Capri</h3></div>
  <div class="cat-card"><div class="card-img" role="img" aria-label="Black yoga shoes with green stripes" style="background:linear-gradient(#fff,#e4e8d8)"></div><h3>Yoga Shoes</h3></div>
</div>

<h2 class="abs section-title" style="top:1128px">Featured Products</h2>
<svg class="abs divider" style="top:1177px" viewBox="0 0 170 18"><path d="M0 9h72M98 9h72" stroke="#ccc"/><circle cx="85" cy="9" r="6" fill="none" stroke="#ccc"/><circle cx="85" cy="9" r="2.5" fill="none" stroke="#ccc"/></svg>

<svg width="0" height="0" style="position:absolute">
  <defs>
    <path id="star" d="M4 0l1.2 2.6 2.8.3-2.1 1.9.6 2.8L4 6.2 1.5 7.6l.6-2.8L0 2.9l2.8-.3z"/>
    <g id="cart"><path d="M1 2h2l2 6h6l1-4H4" fill="none" stroke="#000" stroke-width="1.3"/><circle cx="6" cy="10" r="1" /><circle cx="10" cy="10" r="1"/></g>
    <g id="swap"><path d="M2 4h12M11 1l3 3-3 3M14 10H2M5 7l-3 3 3 3" fill="none" stroke="#fff" stroke-width="1.6"/></g>
    <path id="heart" d="M7 12L1.5 6.5A3 3 0 017 2.8a3 3 0 015.5 3.7z" fill="#fff"/>
  </defs>
</svg>

<div class="abs grid" style="top:1235px;gap:18px 16px">
  <div class="prod-card"><div class="card-img" role="img" aria-label="Green yoga tank top with black leggings" style="background:linear-gradient(#fff,#dff0c0)"></div><h4>Yoga Top</h4>
    <div class="rating"><span class="stars"><svg width="8" height="8" fill="var(--star)"><use href="#star"/></svg><svg width="8" height="8" fill="var(--star)"><use href="#star"/></svg><svg width="8" height="8" fill="var(--star)"><use href="#star"/></svg><svg width="8" height="8" fill="var(--star)"><use href="#star"/></svg><svg width="8" height="8" fill="var(--star-off)"><use href="#star"/></svg></span>1 Review(s)</div>
    <div class="price">$16.95</div>
    <div class="actions"><div class="add-cart"><div class="ic"><svg width="14" height="12"><use href="#cart"/></svg></div><span>Add to Cart</span></div><div class="sq"><svg width="16" height="14"><use href="#swap"/></svg></div><div class="sq"><svg width="14" height="13"><use href="#heart"/></svg></div></div></div>
  <div class="prod-card"><div class="card-img" role="img" aria-label="Pink patterned yoga capri" style="background:linear-gradient(#fff,#f3d4df)"></div><h4>Yoga Capri</h4>
    <div class="rating"><span class="stars"><svg width="8" height="8" fill="var(--star)"><use href="#star"/></svg><svg width="8" height="8" fill="var(--star)"><use href="#star"/></svg><svg width="8" height="8" fill="var(--star)"><use href="#star"/></svg><svg width="8" height="8" fill="var(--star)"><use href="#star"/></svg><svg width="8" height="8" fill="var(--star-off)"><use href="#star"/></svg></span>1 Review(s)</div>
    <div class="price">$ 20.00</div>
    <div class="actions"><div class="add-cart"><div class="ic"><svg width="14" height="12"><use href="#cart"/></svg></div><span>Add to Cart</span></div><div class="sq"><svg width="16" height="14"><use href="#swap"/></svg></div><div class="sq"><svg width="14" height="13"><use href="#heart"/></svg></div></div></div>
  <div class="prod-card"><div class="card-img" role="img" aria-label="Black yoga leggings" style="background:linear-gradient(#fff,#e0e0e0)"></div><h4>Yoga Leggings</h4>
    <div class="rating"><span class="stars"><svg width="8" height="8" fill="var(--star)"><use href="#star"/></svg><svg width="8" height="8" fill="var(--star)"><use href="#star"/></svg><svg width="8" height="8" fill="var(--star)"><use href="#star"/></svg><svg width="8" height="8" fill="var(--star)"><use href="#star"/></svg><svg width="8" height="8" fill="var(--star-off)"><use href="#star"/></svg></span>1 Review(s)</div>
    <div class="price">$ 22.50</div>
    <div class="actions"><div class="add-cart"><div class="ic"><svg width="14" height="12"><use href="#cart"/></svg></div><span>Add to Cart</span></div><div class="sq"><svg width="16" height="14"><use href="#swap"/></svg></div><div class="sq"><svg width="14" height="13"><use href="#heart"/></svg></div></div></div>
  <div class="prod-card"><div class="card-img" role="img" aria-label="Black yoga pant with yellow waistband and sports top" style="background:linear-gradient(#fff,#eeeac8)"></div><h4>Yoga T-shirt &amp; Pant</h4>
    <div class="rating"><span class="stars"><svg width="8" height="8" fill="var(--star)"><use href="#star"/></svg><svg width="8" height="8" fill="var(--star)"><use href="#star"/></svg><svg width="8" height="8" fill="var(--star)"><use href="#star"/></svg><svg width="8" height="8" fill="var(--star)"><use href="#star"/></svg><svg width="8" height="8" fill="var(--star-off)"><use href="#star"/></svg></span>1 Review(s)</div>
    <div class="price">$ 18.95</div>
    <div class="actions"><div class="add-cart"><div class="ic"><svg width="14" height="12"><use href="#cart"/></svg></div><span>Add to Cart</span></div><div class="sq"><svg width="16" height="14"><use href="#swap"/></svg></div><div class="sq"><svg width="14" height="13"><use href="#heart"/></svg></div></div></div>

  <div class="prod-card"><div class="card-img" role="img" aria-label="Pink yoga tank top" style="background:linear-gradient(#fff,#f8cfe0)"></div><h4>Yoga T-shirt</h4>
    <div class="rating"><span class="stars"><svg width="8" height="8" fill="var(--star)"><use href="#star"/></svg><svg width="8" height="8" fill="var(--star)"><use href="#star"/></svg><svg width="8" height="8" fill="var(--star)"><use href="#star"/></svg><svg width="8" height="8" fill="var(--star)"><use href="#star"/></svg><svg width="8" height="8" fill="var(--star-off)"><use href="#star"/></svg></span>1 Review(s)</div>
    <div class="price">$ 30.95</div>
    <div class="actions"><div class="add-cart"><div class="ic"><svg width="14" height="12"><use href="#cart"/></svg></div><span>Add to Cart</span></div><div class="sq"><svg width="16" height="14"><use href="#swap"/></svg></div><div class="sq"><svg width="14" height="13"><use href="#heart"/></svg></div></div></div>
  <div class="prod-card"><div class="card-img" role="img" aria-label="Blue lycra yoga pants" style="background:linear-gradient(#fff,#cfdaf4)"></div><h4>Yoga Lycra Pants</h4>
    <div class="rating"><span class="stars"><svg width="8" height="8" fill="var(--star)"><use href="#star"/></svg><svg width="8" height="8" fill="var(--star)"><use href="#star"/></svg><svg width="8" height="8" fill="var(--star)"><use href="#star"/></svg><svg width="8" height="8" fill="var(--star-off)"><use href="#star"/></svg><svg width="8" height="8" fill="var(--star-off)"><use href="#star"/></svg></span>1 Review(s)</div>
    <div class="price">$ 28.95</div>
    <div class="actions"><div class="add-cart"><div class="ic"><svg width="14" height="12"><use href="#cart"/></svg></div><span>Add to Cart</span></div><div class="sq"><svg width="16" height="14"><use href="#swap"/></svg></div><div class="sq"><svg width="14" height="13"><use href="#heart"/></svg></div></div></div>
  <div class="prod-card"><div class="card-img" role="img" aria-label="Woman wearing a black camisole and pants" style="background:linear-gradient(#fff,#dedede)"></div><h4>Yoga Women's Cami</h4>
    <div class="rating"><span class="stars"><svg width="8" height="8" fill="var(--star)"><use href="#star"/></svg><svg width="8" height="8" fill="var(--star)"><use href="#star"/></svg><svg width="8" height="8" fill="var(--star)"><use href="#star"/></svg><svg width="8" height="8" fill="var(--star)"><use href="#star"/></svg><svg width="8" height="8" fill="var(--star-off)"><use href="#star"/></svg></span>1 Review(s)</div>
    <div class="price">$ 24.95</div>
    <div class="actions"><div class="add-cart"><div class="ic"><svg width="14" height="12"><use href="#cart"/></svg></div><span>Add to Cart</span></div><div class="sq"><svg width="16" height="14"><use href="#swap"/></svg></div><div class="sq"><svg width="14" height="13"><use href="#heart"/></svg></div></div></div>
  <div class="prod-card"><div class="card-img" role="img" aria-label="Dark burgundy yoga capri" style="background:linear-gradient(#fff,#e2d4d6)"></div><h4>Yoga Capri</h4>
    <div class="rating"><span class="stars"><svg width="8" height="8" fill="var(--star)"><use href="#star"/></svg><svg width="8" height="8" fill="var(--star)"><use href="#star"/></svg><svg width="8" height="8" fill="var(--star)"><use href="#star"/></svg><svg width="8" height="8" fill="var(--star-off)"><use href="#star"/></svg><svg width="8" height="8" fill="var(--star-off)"><use href="#star"/></svg></span>1 Review(s)</div>
    <div class="price">$ 19.95</div>
    <div class="actions"><div class="add-cart"><div class="ic"><svg width="14" height="12"><use href="#cart"/></svg></div><span>Add to Cart</span></div><div class="sq"><svg width="16" height="14"><use href="#swap"/></svg></div><div class="sq"><svg width="14" height="13"><use href="#heart"/></svg></div></div></div>
</div>

<section class="abs band">
  <h2>BE THE FIRST TO KNOW</h2>
  <p>Sign up for the latest news, new releases and special promotions.</p>
  <div class="btn">Sign Up</div>
</section>

<div class="abs services">
  <div class="service">
    <svg width="34" height="26" viewBox="0 0 34 26"><rect x="1" y="3" width="19" height="15" fill="#000"/><path d="M21 8h7l5 6v4H21z" fill="#000"/><circle cx="8" cy="21" r="3.5" fill="#000" stroke="#fff" stroke-width="1.5"/><circle cx="26" cy="21" r="3.5" fill="#000" stroke="#fff" stroke-width="1.5"/></svg>
    <h5>Free Shipping</h5><p>On order over $ 120.00</p>
  </div>
  <div class="service">
    <svg width="30" height="28" viewBox="0 0 30 28"><rect x="2" y="8" width="26" height="6" fill="#000"/><rect x="4" y="15" width="22" height="12" fill="#000"/><rect x="13" y="8" width="4" height="19" fill="#fff"/><path d="M15 8c-3-6-9-6-8-2 1 2 5 2 8 2 3 0 7 0 8-2 1-4-5-4-8 2z" fill="none" stroke="#000" stroke-width="2"/></svg>
    <h5>Discount On Orders</h5><p>Vyngle wine consequat odio sed.</p>
  </div>
  <div class="service">
    <svg width="30" height="28" viewBox="0 0 30 28"><circle cx="14" cy="9" r="6" fill="#000"/><path d="M6 9a8 8 0 0116 0" fill="none" stroke="#000" stroke-width="2"/><path d="M2 27c0-7 5-10 12-10s12 3 12 10z" fill="#000"/><circle cx="24" cy="22" r="4" fill="#fff" stroke="#000" stroke-width="1.5"/></svg>
    <h5>Need On Help</h5><p>On order over $111.00 any Time</p>
  </div>
</div>

<footer class="abs footer">
  <div class="fcol" style="left:83px"><h6>Quick Links</h6>
    <ul><li>Home</li><li>About</li><li>Inspiration</li><li>Featured Products</li><li>Blog</li><li>Contact Us</li></ul></div>
  <div class="vsep" style="left:296px"></div>
  <div class="fcol" style="left:320px"><h6>Information</h6>
    <ul><li>About Us</li><li>Customer Service</li><li>New Collection</li><li>Privacy Policy</li><li>Terms &amp; Condition</li><li>Blog</li></ul></div>
  <div class="vsep" style="left:517px"></div>
  <div class="fcol news" style="left:589px"><h6 style="width:260px">Newsletter Sign-up</h6>
    <p>Lorem ipsum dolor sit amet, consecte adipiscing elit</p>
    <div class="field">Enter your Email Address</div>
    <div class="submit">Submit</div></div>
  <div class="vsep" style="left:916px"></div>
  <div class="foot-brand">vey</div>
  <div class="social"><span></span><span></span><span></span><span></span></div>
</footer>

<div class="abs bottombar">
  <div class="copy">Copyright © 2016 Vey. All Rights Reserved.</div>
  <div class="accept"><b>We Accept :</b>
    <span class="card-pay">Nira</span><span class="card-pay">Orbi</span><span class="card-pay">Luma</span><span class="card-pay">Tesca</span><span class="card-pay">Quill</span>
  </div>
</div>

</body>
</html>
```